Verpackungsdesign für Wellness- und Saunaprodukte
Zielgruppe
BaFinn ist ein junges Start-Up, das sich auf Wellness- und Saunaprodukte spezialisiert hat. Unsere Zielgruppe besteht zu beinahe gleichen Teilen aus männlichen und weiblichen Personen zwischen 30 und 60 Jahren. Unsere Produkte befinden sich eher im mittel- bis höherpreisigen Segment, daher streben wir ein hochwertiges Design für unsere Verpackungen an. Unsere Produktpalette reicht von Mentholkristallen, Saunaaufgüssen, bis hin zu Textilien für den Wellnessbereich und soll dementsprechend Menschen ansprechen, die sich einen gewissen Luxus im Alltag auch gönnen.
Aufgabenstellung
Inspiriert von der skandinavischen Sauna Kultur, möchten wir Momente der Erholung und
Entspannung in den Alltag unserer Kunden bringen. Die Geschichte des Saunierens ist eng mit der skandinavischen Kultur verbunden und skandinavische Stilelemente sind zeitgemäß und sprechen ein breites Publikum an. Das Design muss auf Dosen/Tiegel , Karton Verpackungen und Flaschen verschiedener Größen adaptierbar sein (siehe Bild im Anhang).
40g Tiegel(transparent) Höhe 40mm Durchmesser 60mm (ohne Deckel Silber gebürstet)
100g Tiegel(transparent) Höhe 53mm Durchmesser 71mm (ohne Deckel Silber gebürstet)
200g Tiegel(transparent) Höhe 65mm Durchmesser 90mm (ohne Deckel Silber gebürstet)
Karton Verpackung 124,5x49x49mm
Karton Verpackung 100x100x100mm
Flaschenetikett 134x67mm (Braunglas, schwarzer Deckel)
Es soll ein passendes Keyvisual erstellt werden.
Im Anhang sieht man die Verpackungen, Dosen, Flaschen sowie unsere ersten Design Entwürfe (an diese Anordnung der Elemente kann sich der Designer orientieren ). Das Logo bleibt wie gegeben. Das Produkt für die Tiegel soll Mentholkristalle sein.

```html
<!DOCTYPE html>
<html lang="de">
<head>
<meta charset="utf-8">
<title>BaFinn – Verpackungsdesign Sauna &amp; Wellness</title>
<link rel="stylesheet" href="https://fonts.googleapis.com/css2?family=Tenor+Sans&display=swap">
<style>
  :root {
    --bg: #e9e9e8;
    --ink: #2b2b29;
    --line: #f4f4f1;
    --sage: #a9ad97;
    --stone: #a7a7a5;
    --rose: #c8968a;
    --font: "Tenor Sans", "Gill Sans", sans-serif;
  }
  * { box-sizing: border-box; margin: 0; padding: 0; }
  html, body { width: 1200px; height: 603px; overflow: hidden; }
  body {
    background: var(--bg);
    font-family: var(--font);
    color: var(--ink);
    position: relative;
  }
  .label {
    position: absolute;
    overflow: hidden;
    display: flex;
    flex-direction: column;
    align-items: center;
    text-align: center;
  }
  .leaf-art {
    position: absolute;
    inset: 0;
    pointer-events: none;
  }
  .brand {
    display: flex;
    flex-direction: column;
    align-items: center;
    gap: 2px;
    position: relative;
  }
  .brand-dot {
    width: 13px; height: 13px;
    border: 1.4px solid var(--ink);
    border-radius: 50%;
  }
  .brand-name { font-size: 7px; letter-spacing: 0.3px; }
  .product-name {
    position: relative;
    font-size: 15px;
    letter-spacing: 0.6px;
    line-height: 1.35;
    text-transform: uppercase;
  }
  .product-use {
    position: relative;
    font-size: 7.5px;
    letter-spacing: 1.2px;
    line-height: 1.6;
    text-transform: uppercase;
  }

  /* Faltschachtel 124,5 x 49 x 49 mm – Vorderseite */
  .carton-front {
    left: 170px; top: 150px; width: 126px; height: 320px;
    background: var(--sage);
    padding-top: 36px;
  }
  .carton-front .product-name { margin-top: 92px; }
  .carton-front .product-use { margin-top: auto; margin-bottom: 16px; }

  /* Flaschenetikett 134 x 67 mm */
  .bottle-label {
    left: 326px; top: 245px; width: 118px; height: 225px;
    background: var(--sage);
    padding-top: 22px;
  }
  .bottle-label .product-name { margin-top: 22px; }
  .bottle-label .product-use { margin-top: auto; margin-bottom: 18px; }

  /* Tiegeletiketten */
  .jar-label {
    top: 350px; width: 240px; height: 120px;
    padding-top: 22px;
  }
  .jar-label .product-name { margin-top: 12px; font-size: 14.5px; }
  .jar-label .product-use { margin-top: 2px; }
  .jar-menthol { left: 476px; background: var(--stone); }
  .jar-peeling { left: 758px; background: var(--rose); }
</style>
</head>
<body>

  <section class="label carton-front">
    <div class="leaf-art" role="img" aria-label="Feine weiße Linienzeichnung von Blattzweigen"
         style="background: linear-gradient(160deg, rgba(255,255,255,0.12) 0%, rgba(255,255,255,0) 45%, rgba(255,255,255,0.1) 100%);"></div>
    <div class="brand"><span class="brand-dot"></span><span class="brand-name">BaFinn</span></div>
    <h2 class="product-name">Nordische<br>Fichte</h2>
    <p class="product-use">Aufguss<br>für die Sauna</p>
  </section>

  <section class="label bottle-label">
    <div class="leaf-art" role="img" aria-label="Feine weiße Linienzeichnung von Blattzweigen"
         style="background: linear-gradient(200deg, rgba(255,255,255,0.12) 0%, rgba(255,255,255,0) 50%, rgba(255,255,255,0.1) 100%);"></div>
    <div class="brand"><span class="brand-dot"></span><span class="brand-name">BaFinn</span></div>
    <h2 class="product-name">Nordische<br>Fichte</h2>
    <p class="product-use">Aufguss<br>für die Sauna</p>
  </section>

  <section class="label jar-label jar-menthol">
    <div class="leaf-art" role="img" aria-label="Feine weiße Linienzeichnung von Blattzweigen"
         style="background: linear-gradient(90deg, rgba(255,255,255,0.12) 0%, rgba(255,255,255,0) 25%, rgba(255,255,255,0) 75%, rgba(255,255,255,0.12) 100%);"></div>
    <div class="brand"><span class="brand-dot"></span><span class="brand-name">BaFinn</span></div>
    <h2 class="product-name">Mentholkristalle</h2>
    <p class="product-use">Für die Sauna</p>
  </section>

  <section class="label jar-label jar-peeling">
    <div class="leaf-art" role="img" aria-label="Feine weiße Linienzeichnung von Blattzweigen"
         style="background: linear-gradient(90deg, rgba(255,255,255,0.12) 0%, rgba(255,255,255,0) 25%, rgba(255,255,255,0) 75%, rgba(255,255,255,0.12) 100%);"></div>
    <div class="brand"><span class="brand-dot"></span><span class="brand-name">BaFinn</span></div>
    <h2 class="product-name">Granatapfel-Peeling</h2>
    <p class="product-use">Meersalz für den Körper</p>
  </section>

</body>
</html>
```